Solvaquinta Unique Gift Certificate

We need a unique, luxury gift certificate created for our online company (Solvaquinta). We are looking for something out of the ordinary, ie. do not want it to look like a 'normal' gift certificate. Please visit our website to gain a feel for our company (solvaquinta.com.au). The dimensions are 148x148mm. We need our logo, website details, to, from, description, code, exp date included. The certificate will be printed on wood veneer so watermarks will not work. We want it to be clean and minimalistic.

Industry/Entity Type

It Company

```html
<!DOCTYPE html>
<html lang="en">
<head>
<meta charset="utf-8">
<title>Solvaquinta Gift Certificate</title>
<link href="https://fonts.googleapis.com/css2?family=Great+Vibes&family=Raleway:wght@300;400&display=swap" rel="stylesheet">
<style>
  :root {
    --page-bg: #ecebe8;
    --veneer-light: #f0dfb8;
    --veneer-mid: #e6cf9f;
    --veneer-dark: #dcc08b;
    --panel-fill: #d8b98a;
    --panel-edge: #f1e1bf;
    --ink-brown: #9a6438;
    --ink-soft: #a07a55;
    --rule: #b58d62;
    --sprig: #9c8a5a;
    --logo-bg: #ffffff;
    --logo-ink: #2f8fb3;
  }
  html, body {
    margin: 0;
    width: 1200px;
    height: 927px;
    overflow: hidden;
    background: var(--page-bg);
  }
  .certificate {
    position: absolute;
    left: 160px;
    top: 133px;
    width: 880px;
    height: 660px;
    background:
      repeating-linear-gradient(90deg, rgba(160,120,60,0.05) 0 2px, transparent 2px 9px),
      linear-gradient(100deg, var(--veneer-light), var(--veneer-mid) 55%, var(--veneer-dark));
    box-shadow: 0 6px 24px rgba(0,0,0,0.15);
    font-family: "Raleway", sans-serif;
  }
  .certificate__art {
    position: absolute;
    inset: 0;
  }
  .certificate__title {
    position: absolute;
    left: 120px;
    top: 38px;
    margin: 0;
    font-family: "Great Vibes", cursive;
    font-weight: 400;
    font-size: 72px;
    color: var(--ink-brown);
  }
  .sprig {
    position: absolute;
    height: 14px;
    border-radius: 7px;
    background: linear-gradient(90deg, transparent, var(--sprig), transparent);
    opacity: 0.7;
  }
  .sprig--title { left: 30px; top: 88px; width: 86px; }
  .sprig--top { left: 420px; top: 40px; width: 260px; }
  .sprig--footer { left: 30px; top: 612px; width: 70px; }
  .field-label {
    position: absolute;
    font-size: 30px;
    font-weight: 300;
    color: var(--ink-soft);
    letter-spacing: 1px;
  }
  .field-label--small { font-size: 20px; }
  .brand-tile {
    position: absolute;
    right: 30px;
    top: 24px;
    width: 128px;
    height: 112px;
    background: var(--logo-bg);
    display: flex;
    flex-direction: column;
    align-items: center;
    justify-content: center;
    gap: 10px;
  }
  .brand-tile__square {
    width: 36px;
    height: 36px;
    border: 3px solid var(--logo-ink);
    border-radius: 50%;
  }
  .brand-tile__name {
    font-size: 17px;
    font-weight: 400;
    color: var(--logo-ink);
  }
  .certificate__website {
    position: absolute;
    left: 110px;
    top: 582px;
    margin: 0;
    font-size: 50px;
    font-weight: 300;
    letter-spacing: 3px;
    color: var(--ink-soft);
  }
</style>
</head>
<body>
  <section class="certificate">
    <svg class="certificate__art" width="880" height="660" viewBox="0 0 880 660">
      <path class="panel" d="M110 150 H770 A40 40 0 0 0 810 190 V510 A40 40 0 0 0 770 550 H110 A40 40 0 0 0 70 510 V190 A40 40 0 0 0 110 150 Z"
            fill="#d8b98a" fill-opacity="0.75" stroke="#f1e1bf" stroke-width="3"/>
      <g class="rules" stroke="#b58d62" stroke-width="1.5">
        <line x1="140" y1="215" x2="770" y2="215"/>
        <line x1="140" y1="265" x2="770" y2="265"/>
        <line x1="160" y1="320" x2="770" y2="320"/>
        <line x1="215" y1="375" x2="770" y2="375"/>
        <line x1="300" y1="430" x2="770" y2="430"/>
        <line x1="205" y1="490" x2="520" y2="490"/>
      </g>
    </svg>

    <div class="sprig sprig--title" role="img" aria-label="Leafy sprig ornament"></div>
    <div class="sprig sprig--top" role="img" aria-label="Trailing vine ornament"></div>
    <h1 class="certificate__title">Gift Certificate</h1>

    <div class="brand-tile">
      <span class="brand-tile__square"></span>
      <span class="brand-tile__name">Solvaquinta</span>
    </div>

    <span class="field-label" style="left:100px; top:288px;">To:</span>
    <span class="field-label" style="left:100px; top:343px;">From:</span>
    <span class="field-label" style="left:100px; top:398px;">Description:</span>
    <span class="field-label" style="left:100px; top:458px;">Code:</span>
    <span class="field-label field-label--small" style="left:560px; top:466px;">Expiration Date</span>

    <div class="sprig sprig--footer" role="img" aria-label="Leafy sprig ornament"></div>
    <p class="certificate__website">solvaquinta.com.au</p>
  </section>
</body>
</html>
```